ULMIRA card Technical Architecture

Hello everyone ULMIRA: It is a consulting firm in Architecture and Construction. I require a card duplexing, sober, elegant, classic but not boring. Update 1: Use the following data for the card. Name: Gonzalo Pereda Mauricio Villalta Position: COO Twitter: @ulmiraAT Homepage: ulmira-example.com home address not include the participation of all thank you.

Target Market(s)

Construction companies, Architects and Consulting Engineers

Industry/Entity Type

Consulting

Contact Information for Business Card

Los campos que debe tener:
Nombre, Cargo, email, homepage y twitter

Font styles to use
Serif
Sans Serif
Other font styles liked:
• Me gustan playfair display, open sans y roboto, pero estoy sujeto a sus propuestas

Requirements
Must have
• Colors: Present combined proposals in white, red, gray and black Update 1: The two names must be clearly differentiated from the two surnames
Nice to have
• They are free to present their best proposals. I will bring them immediate feedback to the extent you can go see their designs. Complete data for card and logo files will give the winner the

```html
<!DOCTYPE html>
<html lang="es">
<head>
<meta charset="utf-8">
<title>ULMIRA – Business Card</title>
<link href="https://fonts.googleapis.com/css2?family=Open+Sans:wght@400;600;700&display=swap" rel="stylesheet">
<style>
  :root {
    --stage: #161616;
    --paper: #ffffff;
    --brand-red: #b3121a;
    --deep-red: #8a0d12;
    --pattern-red: #9a1016;
    --ink: #222222;
    --soft-white: #f3e9e9;
  }
  html, body {
    margin: 0;
    padding: 0;
    width: 1200px;
    height: 900px;
    overflow: hidden;
    background: var(--stage);
    font-family: "Open Sans", Arial, sans-serif;
  }
  .stage {
    position: relative;
    width: 1200px;
    height: 900px;
  }
  .card {
    position: absolute;
    top: 306px;
    width: 439px;
    height: 271px;
    border-radius: 12px;
    overflow: hidden;
  }
  .card--front {
    left: 149px;
    background: var(--paper);
  }
  .card--back {
    left: 609px;
    background: var(--deep-red);
  }
  .front-brand {
    position: absolute;
    left: 48px;
    top: 118px;
    width: 140px;
    text-align: center;
    color: var(--brand-red);
    font-weight: 700;
    font-size: 26px;
    letter-spacing: 1px;
  }
  .contact {
    position: absolute;
    left: 229px;
    top: 66px;
    color: var(--ink);
  }
  .contact__name {
    margin: 0;
    color: var(--brand-red);
    font-weight: 600;
    font-size: 17px;
    line-height: 22px;
  }
  .contact__role {
    margin: 0 0 14px;
    font-size: 12px;
    line-height: 16px;
  }
  .contact__line {
    display: flex;
    align-items: center;
    font-size: 12px;
    line-height: 16px;
    margin: 0;
  }
  .contact__line--small .icon { width: 8px; height: 8px; margin: 0 8px 0 0; }
  .contact__gap { height: 16px; }
  .icon {
    display: inline-block;
    width: 15px;
    height: 15px;
    margin-right: 7px;
    flex: none;
  }
  .contact__line--web { font-size: 12.5px; line-height: 18px; }
  .back-pattern {
    position: absolute;
    inset: 0;
    background: radial-gradient(ellipse at center, #a3141b 0%, var(--pattern-red) 55%, #7d0b10 100%);
  }
  .back-brand {
    position: absolute;
    left: 0;
    right: 0;
    top: 150px;
    text-align: center;
    color: var(--paper);
  }
  .back-brand__name {
    margin: 0;
    font-weight: 400;
    font-size: 34px;
    line-height: 36px;
    letter-spacing: 9px;
    padding-left: 9px;
  }
  .back-brand__rule {
    width: 250px;
    height: 1px;
    margin: 2px auto 3px;
    background: var(--soft-white);
    opacity: 0.8;
  }
  .back-brand__tagline {
    margin: 0;
    font-size: 11px;
    letter-spacing: 3.2px;
    text-transform: uppercase;
  }
</style>
</head>
<body>
<main class="stage">
  <section class="card card--front" aria-label="Card front">
    <div class="front-brand">ULMIRA</div>
    <div class="contact">
      <p class="contact__name">TOMAS RIVERA</p>
      <p class="contact__role">Managing Director</p>
      <p class="contact__line contact__line--small">
        <svg class="icon" viewBox="0 0 8 8" aria-hidden="true"><rect x="1.5" y="0" width="5" height="8" rx="1" fill="#b3121a"/><rect x="2.5" y="1" width="3" height="5" fill="#fff"/></svg>
        (044)555010203
      </p>
      <p class="contact__line contact__line--small">
        <svg class="icon" viewBox="0 0 8 8" aria-hidden="true"><rect x="0" y="1.5" width="8" height="5.5" fill="#b3121a"/><polyline points="0,1.5 4,4.5 8,1.5" fill="none" stroke="#fff" stroke-width="0.8"/></svg>
        info@ulmira-mail.com
      </p>
      <div class="contact__gap"></div>
      <p class="contact__line contact__line--web">
        <svg class="icon" viewBox="0 0 15 15" aria-hidden="true"><rect width="15" height="15" rx="2" fill="#b3121a"/></svg>
        www.social-example.com
      </p>
      <p class="contact__line contact__line--web">
        <svg class="icon" viewBox="0 0 15 15" aria-hidden="true"><rect width="15" height="15" rx="2" fill="#b3121a"/><circle cx="7.5" cy="7.5" r="4" fill="none" stroke="#fff" stroke-width="1.2"/></svg>
        www.sitename-example.com
      </p>
    </div>
  </section>

  <section class="card card--back" aria-label="Card back">
    <div class="back-pattern" role="img" aria-label="Subtle repeating triangle pattern in deep red tones"></div>
    <div class="back-brand">
      <p class="back-brand__name">ULMIRA</p>
      <div class="back-brand__rule"></div>
      <p class="back-brand__tagline">Arquitectura Técnica</p>
    </div>
  </section>
</main>
</body>
</html>
```